New B2C website design to help dads be better dads

DadHarbor is a website to help dads be the “best dad you can be.”

We require our website to be designed into a PSD format, no coding necessary.

The general concept is a two-page design. The first page is the login page, the second page is the home page. Once at the home page, rather than navigating to and from different pages, the user will push and pull through different visual and functional layers of the hierarchy. In theory, this should add to the user experience by having a visual anchor of where they are (through layered pagination) as well as improving loading times since the new information should only be a delta in data load versus a brand new page load.

The general look-and-feel we are going for is clean, simple, minimal. This means that the winning design will show us a good eye for web-optimized typography, good use of white (negative) space, and good use of a visually pleasing grid.

We require a total of 6 page "views" plus the landing page. We note that many of the views are similar to one another.
Landing page
Milestone view
Task view
Content view, articles
Content view, products
Search view
What's new view

Please review all of the additional information provided as well as the attachments for examples.

We provide the following websites as good references for:

Typography:
http://example-kelvorn.com/journal/

Use of white space:
http://www.trenvaskit.com/
http://moldrefin.com/

Example for “scrolling” page concept as well as good balance of color, typography, and white space:
http://www.qorbitalmeet.eu/

Please contact us with questions so that we can guide your design effort.
Updates

Hello designers,

The following information is added to help guide the design process:

1.  For the text dialogue below the landing page, please assume the following word count:
"why are we making dad harbor?": 250 words
"who are we?" 200 words
"what's the deal with the penguin logo?" 300 words

For the social media links, please see http://www.gravelplumbs.com/
Notice the floating "social" bar that is always to the right.  This is the concept we are going for, please try to implement this as you see fit. 

Target Market(s)

Fathers of young children ages 0-6 years old.

Industry/Entity Type

Product

Font styles to use
Sans Serif

Requirements
Must have
• Clean lines, minimal design concept

Incorporation of our logo (see attached document)

Header content is static for all views after landing page, see example

This page WILL be responsive, please keep that in mind when designing
The timeline bar should be to the left, with the timeline bar’s “milestones” also being responsive.

Designer is free to suggest font types, but any fonts used must be royalty-free and web-optimized. We request a minimum number of font types as well as fonts that load relatively fast. We reinforce that visually appealing typography is a significant factor in the winning design choice.

While we are not expecting the winning design to include code, please keep in mind that the final implementation needs to be optimized for desktop, tablet, and mobile platforms.

If you are using stock photography that is not generated by you, please provide where/how we can obtain imagery, as well as price.

All custom graphics must be available in original formats; Photoshop/GIMP layered files for layout design, and vector formats for logos, icons and other graphical elements.

Please incorporate “Blue” into design elements as you see fit, as the RGB 67 74 169 Blue is the primary color used in our brand. The complement to this blue is 255 202 0, a brownish orange. Feel free to use this color as well, although please keep it to a lesser amount.

Background color is your choice, do not feel the need to use the grey.
Should not have
• Excessive graphical content such that it affects loading times

Excessive use of too many font types such that it affects loading times

```html
<!DOCTYPE html>
<html lang="en">
<head>
<meta charset="utf-8">
<title>DadHarbor – Be the best dad you can be</title>
<link href="https://fonts.googleapis.com/css2?family=Bebas+Neue&family=Open+Sans:wght@300;400;600;700&display=swap" rel="stylesheet">
<style>
:root{
  --brand-blue:#434aa9;
  --navy:#1f2a6b;
  --navy-glass:rgba(24,34,96,.88);
  --gold:#ffca00;
  --ink:#1c1c1c;
  --white:#ffffff;
  --muted:#555a66;
}
*{box-sizing:border-box;margin:0;padding:0}
html,body{width:1200px;height:3151px;overflow:hidden}
body{background:var(--white);font-family:"Open Sans",Arial,sans-serif;color:var(--ink);position:relative}

/* HERO */
.hero{position:absolute;left:0;top:0;width:1200px;height:704px;
  background:linear-gradient(115deg,#7f9a4c 0%,#b7c98a 22%,#d9a585 42%,#b9876a 58%,#6f5a44 80%,#4a3a2c 100%)}
.hero-photo{position:absolute;inset:0}
.brand{position:absolute;left:31px;top:24px;display:flex;align-items:center;gap:10px}
.brand-dot{width:34px;height:34px;border-radius:50%;background:var(--navy)}
.brand-name{font-family:"Open Sans",sans-serif;font-weight:700;font-size:22px;color:var(--navy)}
.tagline{position:absolute;left:0;top:200px;width:718px;height:115px;background:var(--navy-glass);padding:10px 0 0 28px;white-space:nowrap;overflow:hidden}
.tagline-title{font-family:"Bebas Neue",sans-serif;font-weight:400;font-size:66px;line-height:62px;color:var(--gold);letter-spacing:1px}
.tagline-sub{font-family:"Open Sans",sans-serif;font-weight:600;font-size:25px;line-height:34px;color:var(--white)}
.login{position:absolute;left:31px;top:315px;width:308px;height:242px;background:var(--navy-glass);padding:12px 16px;border-radius:0 0 6px 6px}
.field{display:flex;align-items:center;gap:8px;height:46px;border:1px solid #6f7bd0;border-radius:4px;background:rgba(40,52,140,.8);padding:0 12px;margin-bottom:20px;color:var(--white);font-size:16px}
.forgot{font-size:12px;color:var(--white);margin:-8px 0 14px}
.signin{display:block;width:276px;height:46px;border:0;border-radius:4px;background:var(--gold);color:var(--navy);font-family:"Open Sans",sans-serif;font-weight:700;font-size:15px}
.share{position:absolute;right:0;top:184px;width:52px;height:262px;background:var(--gold);border-radius:8px 0 0 8px;padding-top:8px;text-align:center}
.share-label{font-size:12px;color:var(--navy);margin-bottom:6px}
.share-btn{display:block;width:40px;height:40px;border-radius:50%;background:var(--navy);margin:0 auto 14px}
.scroll-cue{position:absolute;left:579px;top:632px}

/* ABOUT */
.about-title{position:absolute;left:0;top:748px;width:1200px;text-align:center;font-family:"Open Sans",sans-serif;font-weight:700;font-size:42px;color:var(--brand-blue);letter-spacing:1px}
.story{position:absolute;left:0;width:1200px;overflow:hidden}
.story-photo{position:absolute;top:0;height:100%}
.story-copy{position:absolute;left:31px;width:625px;z-index:1}
.story-heading{font-family:"Open Sans",sans-serif;font-weight:400;font-size:42px;line-height:52px;margin-bottom:12px;white-space:nowrap}
.story-text{font-size:14px;line-height:23.8px}
.story--why{top:861px;height:646px;background:linear-gradient(90deg,#ffffff 0%,#f2f2f2 55%,#e8e6e4 100%)}
.story--why .story-photo{left:630px;width:570px;background:linear-gradient(120deg,#d8c2ae 0%,#b48a6c 40%,#7aa0c8 75%,#4f7cb0 100%)}
.story--why .story-copy{top:50px}
.story--who{top:1507px;height:646px;background:linear-gradient(180deg,#f3f6f9 0%,#c9def0 35%,#6ea9cf 60%,#4d8fbd 75%,#8a7766 100%)}
.story--who .story-photo{left:0;width:1200px;background:linear-gradient(90deg,rgba(255,255,255,.95) 0%,rgba(255,255,255,.75) 45%,rgba(255,255,255,0) 62%)}
.story--who .story-copy{top:56px}
.story--penguin{top:2153px;height:649px;background:var(--brand-blue);color:var(--white)}
.story--penguin .story-copy{top:56px}
.story--penguin .story-heading{white-space:normal;font-size:44px;line-height:50px}
.penguin-mark{position:absolute;left:740px;top:520px;display:flex;align-items:center;gap:14px}
.penguin-dot{width:44px;height:44px;border-radius:50%;background:var(--white)}
.penguin-name{font-weight:700;font-size:36px;color:var(--white)}

/* FOOTER */
.contact{position:absolute;left:0;top:2802px;width:1200px;height:349px;text-align:center}
.contact-kicker{margin-top:48px;font-size:15px;font-weight:600;letter-spacing:4px}
.contact-title{margin-top:14px;font-weight:300;font-size:38px;letter-spacing:3px}
.contact-email{margin-top:14px;font-weight:700;font-size:19px;color:var(--brand-blue)}
.social{margin-top:22px;display:flex;justify-content:center;gap:42px}
.social-btn{width:52px;height:52px;border-radius:50%;background:#e8eaf3}
.legal{margin-top:20px;font-size:13px;color:var(--muted)}
</style>
</head>
<body>

<header class="hero">
  <div class="hero-photo" role="img" aria-label="Photo of a smiling father lying in the grass lifting his child above him"></div>
  <div class="brand"><span class="brand-dot"></span><span class="brand-name">DadHarbor</span></div>
  <div class="tagline">
    <h1 class="tagline-title">BE THE BEST DAD YOU CAN BE</h1>
    <p class="tagline-sub">The portal created exclusively for dads, by dads</p>
  </div>
  <form class="login">
    <div class="field">
      <svg width="18" height="18" viewBox="0 0 18 18"><circle cx="9" cy="5.5" r="4" fill="#ffca00"/><path d="M1 18c0-5 3.5-7.5 8-7.5s8 2.5 8 7.5z" fill="#ffca00"/></svg>
      Username
    </div>
    <div class="field">
      <svg width="18" height="18" viewBox="0 0 18 18"><circle cx="5.5" cy="9" r="4" fill="none" stroke="#ffca00" stroke-width="2.4"/><path d="M9 9h8M14 9v4M17 9v3" stroke="#ffca00" stroke-width="2.4" fill="none"/></svg>
      Password
    </div>
    <p class="forgot">› Forgot login?</p>
    <button class="signin" type="button">SIGN IN / REQUEST ACCESS</button>
  </form>
  <aside class="share">
    <p class="share-label">Share</p>
    <span class="share-btn" aria-label="Share on social network one"></span>
    <span class="share-btn" aria-label="Share on social network two"></span>
    <span class="share-btn" aria-label="Share on social network three"></span>
    <span class="share-btn" aria-label="Share on social network four"></span>
  </aside>
  <svg class="scroll-cue" width="42" height="40" viewBox="0 0 42 40"><path d="M3 4l18 14 18-14" fill="none" stroke="#ffca00" stroke-width="5"/><path d="M3 20l18 14 18-14" fill="none" stroke="#ffca00" stroke-width="5"/></svg>
</header>

<h2 class="about-title">ABOUT DAD HARBOR</h2>

<section class="story story--why">
  <div class="story-photo" role="img" aria-label="Photo of a smiling father carrying his young son on his shoulders"></div>
  <div class="story-copy">
    <h3 class="story-heading">Why are we making dad harbor?</h3>
    <p class="story-text">Lorem ipsum dolor sit amet, consectetur adipisicing elit, sed do eiusmod tempor incididunt ut labore et dolore magna aliqua. Ut enim ad minim veniam, quis nostrud exercitation ullamco laboris nisi ut aliqip ex ea comodo cnsequat. Duis aute irure dolor in rehenderit in voptate velit esse cillum dolore eu fugiat nulla paritur. Excepteur sint occaecat cupidatat non proident, sunt in culpa qui officia deserunt mollit anim id est laborum. Lorem ipsum dolor sit amet, consectetur adipisicing elit, sed do eiusd tmor incididunt ut labore et doore magna aliqua. Ut enim ad minim veniam, quis nistrud exercitation ullamco laboris nisi ut aliquip ex ea comodo cosequat. Duis aute irure dolor in reeherit in volute velit esse cillum dolore eu fugiat nulla paiatur. Excpteur sint occaecat cidatat non proident, sunt in culpa qui officia deserunt molit anim id est laborum. Lorem ipsum door sit met, contur adisicing elit, sed do eiumod tempor incididunt ut labore et dolore magna aliqua. Ut enim ad mnim veniam, quis nostud exercitation ullamco laboris nisi ut aliquip ex ea commodo conequat. Duis aute irure door in repreherit in voluptate velit esse cillum doore eu fugiat nulla pariatur. Excepteur sint occeat cupidatat non proident, sunt in culpa. ex ea commodo consequat. Duis aute irure door in repreherit in voluptate velit esse cillum doore eu fugiat nulla pariatur. Excepteur sint occecat cupiatat non proident, sunt in culpa.</p>
  </div>
</section>

<section class="story story--who">
  <div class="story-photo" role="img" aria-label="Photo of a father and two small children seen from behind, sitting on a pier by the sea"></div>
  <div class="story-copy">
    <h3 class="story-heading">Who are we?</h3>
    <p class="story-text">Lorem ipsum dolor sit amet, consectetur adipisicing elit, sed do eiusmod tempor incididunt ut labore et dolore magna aliqua. Ut enim ad minim veniam, quis nostrud exercitation ullamco laboris nisi ut aliqip ex ea comodo cnsequat. Duis aute irure dolor in rehenderit in voptate velit esse cillum dolore eu fugiat nulla paritur. Excepteur sint occaecat cupidatat non proident, sunt in culpa qui officia deserunt mollit anim id est laborum. Lorem ipsum dolor sit amet, consectetur adipisicing elit, sed do eiusd tmor incididunt ut labore et doore magna aliqua. Ut enim ad minim veniam, quis nistrud exercitation ullamco laboris nisi ut aliquip ex ea comodo cosequat. Duis aute irure dolor in reeherit in volute velit esse cillum dolore eu fugiat nulla paiatur. Excpteur sint occaecat cidatat non proident, sunt in culpa qui officia deserunt molit anim id est laborum. Lorem ipsum door sit met, contur adisicing elit, sed do eiumod tempor incididunt ut labore et dolore magna aliqua. Ut enim ad mnim veniam, quis nostud exercitation ullamco laboris nisi ut aliquip ex ea commodo conequat. Duis aute irure door in repreherit in voluptate velit esse cillum doore eu fugiat nulla pariatur. Excepteur sint occeat cupidatat non proident, sunt in culpa.</p>
  </div>
</section>

<section class="story story--penguin">
  <div class="story-copy">
    <h3 class="story-heading">What's the deal with the<br>penguin logo?</h3>
    <p class="story-text">Lorem ipsum dolor sit amet, consectetur adipisicing elit, sed do eiusmod tempor incididunt ut labore et dolore magna aliqua. Ut enim ad minim veniam, quis nostrud exercitation ullamco laboris nisi ut aliqip ex ea comodo cnsequat. Duis aute irure dolor in rehenderit in voptate velit esse cillum dolore eu fugiat nulla paritur. Excepteur sint occaecat cupidatat non proident, sunt in culpa qui officia deserunt mollit anim id est laborum. Lorem ipsum dolor sit amet, consectetur adipisicing elit, sed do eiusd tmor incididunt ut labore et doore magna aliqua. Ut enim ad minim veniam, quis nistrud exercitation ullamco laboris nisi ut aliquip ex ea comodo cosequat. Duis aute irure dolor in reeherit in volute velit esse cillum dolore eu fugiat nulla paiatur. Excpteur sint occaecat cidatat non proident, sunt in culpa qui officia deserunt molit anim id est laborum. Lorem ipsum door sit met, contur adisicing elit, sed do eiumod tempor incididunt ut labore et dolore magna aliqua. Ut enim ad mnim veniam, quis nostud exercitation ullamco laboris nisi ut aliquip ex ea commodo conequat. Duis aute irure door in repreherit in voluptate velit esse cillum doore eu fugiat nulla pariatur. Excepteur sint occeat cupidatat non proident, sunt in culpa. fugiat nulla pariatur. Excepteur sint occecat cupiatat non proident, sut in culpa.</p>
  </div>
  <div class="penguin-mark"><span class="penguin-dot"></span><span class="penguin-name">DadHarbor</span></div>
</section>

<footer class="contact">
  <p class="contact-kicker">CONTACT</p>
  <h2 class="contact-title">GET IN TOUCH</h2>
  <p class="contact-email">info@dadharbor.com</p>
  <div class="social">
    <span class="social-btn" aria-label="Social network one"></span>
    <span class="social-btn" aria-label="Social network two"></span>
    <span class="social-btn" aria-label="Social network three"></span>
  </div>
  <p class="legal">Privacy Policy &nbsp;|&nbsp; © 2013 DadHarbor &nbsp;|&nbsp; Terms Policy &nbsp;|&nbsp; Disclaimer</p>
</footer>

</body>
</html>
```